Nursing Concepts Diagram

We are looking to make a diagram to represent the Conceptual Framework of our nursing program (college). The frame work is based on three parts:

I. Nursing Process

II. Core Concepts
a. Clinical Competence
b. Critical Thinking
c. Moral/Ethical Principles
d. Growth Mindset
e. Caring/Compassion
f. Cultural Competence
g. Effective Communication
h. Life-long Learning

III. Tavrin's Hierarchy of Needs

I have attached two sketches to give you a sense of how I think this could work.

Please also consider the following:

-Tavrin's Hierarchy of Needs is always represented in the shape of a pyramid so I think the other two components (Nursing Process and Core Concepts) should complement that.

Target Market(s)

Healthcare Professionals, Nursing Educators

Font styles to use
Sans Serif

Colors

Designer to choose colors to be used in the design.

Requirements
Must have
• We would like the diagram to include a legend somewhere on the paper that outlines the parts of each component like demonstrated in the attached table
• All the small parts of the Nursing Process and Tavrin's Hierarchy of Needs don't need to be listed out in the diagram because it may look too wordy, but the eight parts that make up the core concepts should all be listed
• The Nursing Process and Tavrin's Hierachy of needs should both border each of the 8 core concepts so that it can show a relation.

```html
<!DOCTYPE html>
<html lang="en">
<head>
<meta charset="utf-8">
<title>Nursing Program Conceptual Framework</title>
<link rel="stylesheet" href="https://fonts.googleapis.com/css2?family=Poppins:wght@400;500;600&family=Montserrat:wght@600;700&family=Oswald:wght@600&display=swap">
<style>
  :root {
    --paper: #ffffff;
    --heading: #0b5d7e;
    --ink: #222222;
    --frame-blue: #02aaea;
    --lifelong: #f30000;
    --caring: #c0a700;
    --growth: #f76c00;
    --cultural: #22bd00;
    --clinical: #5a4a12;
    --critical: #fdd600;
    --communication: #4a7f78;
    --moral: #3ccfc2;
    --needs-light: #1ccca0;
    --needs-dark: #0f7a5e;
    --needs-text: #fde7f3;
    --label: #ffffff;
  }
  html, body {
    margin: 0;
    padding: 0;
    width: 1200px;
    height: 928px;
    overflow: hidden;
    background: var(--paper);
  }
  .framework {
    display: block;
    width: 1200px;
    height: 928px;
  }
  .legend-heading {
    font-family: "Poppins", sans-serif;
    font-weight: 600;
    font-size: 21px;
    fill: var(--heading);
    letter-spacing: 0.3px;
  }
  .legend-item {
    font-family: "Poppins", sans-serif;
    font-weight: 400;
    font-size: 16px;
    fill: var(--ink);
  }
  .bullet-ring { fill: none; stroke: var(--ink); stroke-width: 1.3; }
  .bullet-dot { fill: var(--ink); }
  .frame-title {
    font-family: "Montserrat", sans-serif;
    font-weight: 700;
    font-size: 66px;
    fill: var(--label);
    letter-spacing: 10px;
  }
  .concept-label {
    font-family: "Montserrat", sans-serif;
    font-weight: 600;
    font-size: 15px;
    fill: var(--label);
    letter-spacing: 1px;
  }
  .base-label {
    font-family: "Montserrat", sans-serif;
    font-weight: 600;
    font-size: 17px;
    fill: var(--label);
    letter-spacing: 1.4px;
  }
  .needs-title {
    font-family: "Oswald", sans-serif;
    font-weight: 600;
    font-size: 47px;
    fill: var(--needs-text);
    letter-spacing: 3px;
  }
</style>
</head>
<body>
<svg class="framework" viewBox="74 12 1253 970" xmlns="http://www.w3.org/2000/svg">
  <defs>
    <linearGradient id="needs-fill" x1="0" y1="0" x2="1" y2="0.3">
      <stop offset="0.35" stop-color="var(--needs-light)"/>
      <stop offset="1" stop-color="var(--needs-dark)"/>
    </linearGradient>
  </defs>

  <!-- Legend -->
  <g class="legend">
    <text class="legend-heading" x="116" y="117">Nursing Process</text>
    <g class="legend-list">
      <g transform="translate(120,147)"><circle class="bullet-ring" r="4.8"/><circle class="bullet-dot" r="2"/></g>
      <text class="legend-item" x="134" y="153">Assessment</text>
      <g transform="translate(120,175)"><circle class="bullet-ring" r="4.8"/><circle class="bullet-dot" r="2"/></g>
      <text class="legend-item" x="134" y="181">Nursing Diagnosis</text>
      <g transform="translate(120,203)"><circle class="bullet-ring" r="4.8"/><circle class="bullet-dot" r="2"/></g>
      <text class="legend-item" x="134" y="209">Planning</text>
      <g transform="translate(120,231)"><circle class="bullet-ring" r="4.8"/><circle class="bullet-dot" r="2"/></g>
      <text class="legend-item" x="134" y="237">Intervention</text>
      <g transform="translate(120,259)"><circle class="bullet-ring" r="4.8"/><circle class="bullet-dot" r="2"/></g>
      <text class="legend-item" x="134" y="265">Evaluation</text>
    </g>

    <text class="legend-heading" x="116" y="316">Core Concepts</text>
    <g class="legend-list">
      <g transform="translate(120,347)"><circle class="bullet-ring" r="4.8"/><circle class="bullet-dot" r="2"/></g>
      <text class="legend-item" x="134" y="353">Clinical Competence</text>
      <g transform="translate(120,375)"><circle class="bullet-ring" r="4.8"/><circle class="bullet-dot" r="2"/></g>
      <text class="legend-item" x="134" y="381">Critical Thinking</text>
      <g transform="translate(120,403)"><circle class="bullet-ring" r="4.8"/><circle class="bullet-dot" r="2"/></g>
      <text class="legend-item" x="134" y="409">Moral/Ethical Principles</text>
      <g transform="translate(120,431)"><circle class="bullet-ring" r="4.8"/><circle class="bullet-dot" r="2"/></g>
      <text class="legend-item" x="134" y="437">Growth Mindset</text>
      <g transform="translate(120,459)"><circle class="bullet-ring" r="4.8"/><circle class="bullet-dot" r="2"/></g>
      <text class="legend-item" x="134" y="465">Caring/Compassion</text>
      <g transform="translate(120,487)"><circle class="bullet-ring" r="4.8"/><circle class="bullet-dot" r="2"/></g>
      <text class="legend-item" x="134" y="493">Cultural Competence</text>
      <g transform="translate(120,514)"><circle class="bullet-ring" r="4.8"/><circle class="bullet-dot" r="2"/></g>
      <text class="legend-item" x="134" y="520">Effective Communication</text>
      <g transform="translate(120,542)"><circle class="bullet-ring" r="4.8"/><circle class="bullet-dot" r="2"/></g>
      <text class="legend-item" x="134" y="548">Life-long Learning</text>
    </g>

    <text class="legend-heading" x="116" y="614">Tavrin’s Hierarchy of Needs</text>
    <g class="legend-list">
      <g transform="translate(120,646)"><circle class="bullet-ring" r="4.8"/><circle class="bullet-dot" r="2"/></g>
      <text class="legend-item" x="134" y="652">Self-actualization</text>
      <g transform="translate(120,674)"><circle class="bullet-ring" r="4.8"/><circle class="bullet-dot" r="2"/></g>
      <text class="legend-item" x="134" y="680">Esteem</text>
      <g transform="translate(120,702)"><circle class="bullet-ring" r="4.8"/><circle class="bullet-dot" r="2"/></g>
      <text class="legend-item" x="134" y="708">Love and Belonging</text>
      <g transform="translate(120,730)"><circle class="bullet-ring" r="4.8"/><circle class="bullet-dot" r="2"/></g>
      <text class="legend-item" x="134" y="736">Safety Needs</text>
      <g transform="translate(120,758)"><circle class="bullet-ring" r="4.8"/><circle class="bullet-dot" r="2"/></g>
      <text class="legend-item" x="134" y="764">Physiological Needs</text>
    </g>
  </g>

  <!-- Pyramid diagram -->
  <g class="pyramid">
    <polygon class="process-frame" points="827,117 1251,852 403,852" fill="var(--frame-blue)"/>

    <polygon class="concept lifelong" points="827,273 725,445 782,470 827,393" fill="var(--lifelong)"/>
    <polygon class="concept caring" points="725,445 625,615 681,640 782,470" fill="var(--caring)"/>
    <polygon class="concept growth" points="625,615 512,807 618,747 681,640" fill="var(--growth)"/>
    <polygon class="concept cultural" points="827,273 955,490 901,518 827,393" fill="var(--cultural)"/>
    <polygon class="concept clinical" points="955,490 1049,650 995,677 901,518" fill="var(--clinical)"/>
    <polygon class="concept critical" points="1049,650 1141,807 1036,747 995,677" fill="var(--critical)"/>
    <polygon class="concept communication" points="512,807 618,747 827,747 827,807" fill="var(--communication)"/>
    <polygon class="concept moral" points="827,747 1036,747 1141,807 827,807" fill="var(--moral)"/>

    <polygon class="needs-core" points="827,393 1036,747 618,747" fill="url(#needs-fill)"/>

    <text class="frame-title" x="0" y="0" text-anchor="middle" transform="translate(652,525) rotate(-60)">NURSING</text>
    <text class="frame-title" x="0" y="0" text-anchor="middle" transform="translate(1022,555) rotate(60)">PROCESS</text>

    <g class="concept-labels">
      <text class="concept-label" text-anchor="middle" transform="translate(781,398) rotate(-60)"><tspan x="0" y="-4">LIFE-LONG</tspan><tspan x="0" y="15">LEARNING</tspan></text>
      <text class="concept-label" text-anchor="middle" transform="translate(710,547) rotate(-60)"><tspan x="0" y="-4">CARING/</tspan><tspan x="0" y="15">COMPASSION</tspan></text>
      <text class="concept-label" text-anchor="middle" transform="translate(612,700) rotate(-60)"><tspan x="0" y="-4">GROWTH</tspan><tspan x="0" y="15">MINDSET</tspan></text>
      <text class="concept-label" text-anchor="middle" transform="translate(875,432) rotate(60)"><tspan x="0" y="-4">CULTURAL</tspan><tspan x="0" y="15">COMPETENCE</tspan></text>
      <text class="concept-label" text-anchor="middle" transform="translate(968,590) rotate(60)"><tspan x="0" y="-4">CLINICAL</tspan><tspan x="0" y="15">COMPETENCE</tspan></text>
      <text class="concept-label" text-anchor="middle" transform="translate(1048,712) rotate(60)"><tspan x="0" y="-4">CRITICAL</tspan><tspan x="0" y="15">THINKING</tspan></text>
      <text class="base-label" text-anchor="middle"><tspan x="708" y="774">EFFECTIVE</tspan><tspan x="708" y="795">COMMUNICATION</tspan></text>
      <text class="base-label" text-anchor="middle"><tspan x="942" y="772">MORAL/</tspan><tspan x="942" y="793">ETHICAL PRINCIPLES</tspan></text>
    </g>

    <text class="needs-title" text-anchor="middle">
      <tspan x="826" y="622">TAVRIN’S</tspan>
      <tspan x="826" y="671">HIERARCHY</tspan>
      <tspan x="822" y="719">OF NEEDS</tspan>
    </text>
  </g>
</svg>
</body>
</html>
```